High-end law practice specializing in closely held business succession planning and complex estates

Solo practitioner whose practice specializes in high-net worth, Legacy & Succession Counsel needs muliple versions of letterhead black and white, please. Letterhead should incorporate slogan, "Guarding Your Family Enterprise is my Calling," for one and "Legacy & Succession Counsel"; third with no slogan. All for The Law Office of Marcy Lynn Pettibone, PC, 418 Cedar Hollow Ln., Larkspur Ridge, Virginia 23648, Tel. 757-555-0142 Fax tbd email: marcy@mlplawgroup.example; Marcy Lynn Pettibone, Esq., principal, licensed in VA, NY, DC
Updates

Project Deadline Extended
Reason: My internet service went down and I can only view designs on my smart phone -- it's just too hard to review. So sorry! Working with my ISP now. Please be patient!

Target Market(s)

High net worth clients with Legacy & Succession Counsel needs, family businesses, family farmers, family foresters -- people with unique estate/succession planning needs who need a specialist who understands them.

Industry/Entity Type

Business

Font styles to use
Script

Requirements
Must have
• A high-end look and feel, connoting trustworthiness, special knowledge, and expertise.

```html
<!DOCTYPE html>
<html lang="en">
<head>
<meta charset="utf-8">
<title>Letterhead – The Law Office of Marcy Lynn Pettibone, PC</title>
<link rel="stylesheet" href="https://fonts.googleapis.com/css2?family=Arimo:wght@400;700&family=PT+Sans:wght@400;700&family=Handlee&display=swap">
<style>
  :root {
    --backdrop: #e6e4e1;
    --paper: #ffffff;
    --ink: #111111;
    --body-grey: #6a6a6a;
    --signature-blue: #1f2a8a;
    --rule: #cfcfcf;
    --divider: #999999;
  }
  * { box-sizing: border-box; margin: 0; padding: 0; }
  html, body {
    width: 953px; height: 1200px; overflow: hidden;
    background: var(--backdrop);
  }
  .letterhead {
    position: absolute; left: 157px; top: 153px;
    width: 638px; height: 895px;
    background: var(--paper);
    box-shadow: 0 4px 10px rgba(0,0,0,.25);
  }
  .firm {
    position: absolute; left: 31px; top: 36px;
    font-family: "Arimo", Arial, sans-serif; color: var(--ink);
  }
  .firm-name {
    font-weight: 700; font-size: 19px; line-height: 21px;
    text-transform: uppercase; letter-spacing: .1px;
  }
  .firm-principal { font-size: 10.5px; margin-top: 3px; }
  .contact {
    position: absolute; left: 423px; top: 28px;
    border-left: 1px solid var(--divider); padding-left: 7px;
    font-family: "PT Sans", sans-serif; font-style: normal;
    font-size: 11.5px; line-height: 17.3px;
    color: var(--ink);
  }
  .contact b { font-weight: 700; }
  .letter {
    position: absolute; left: 31px; top: 246px; width: 578px;
    font-family: "Arimo", Arial, sans-serif; color: var(--body-grey);
    font-size: 13.4px; line-height: 16px;
  }
  .salutation {
    font-family: "PT Sans", sans-serif; font-weight: 700;
    font-size: 14px; margin-bottom: 19px;
  }
  .letter p.body { text-align: justify; margin-bottom: 15px; }
  .closing { margin-top: 40px; }
  .signature {
    font-family: "Handlee", cursive; color: var(--signature-blue);
    font-size: 27px; line-height: 36px; margin: 6px 0 8px;
  }
  .footer {
    position: absolute; left: 33px; right: 30px; top: 848px;
    font-family: "PT Sans", sans-serif; color: var(--ink);
    font-size: 14px; line-height: 16px; text-align: center;
  }
  .footer-rule {
    height: 1px; margin: 2px 0 3px;
    background: linear-gradient(90deg, transparent, var(--rule) 15%, var(--rule) 85%, transparent);
  }
</style>
</head>
<body>
  <main class="letterhead">
    <header>
      <div class="firm">
        <div class="firm-name">The Law Office<br>of Marcy Lynn Pettibone, PC</div>
        <div class="firm-principal">Marcy Lynn Pettibone, Esq., principal, licensed in VA, NY, DC</div>
      </div>
      <address class="contact">
        418 Cedar Hollow Ln.,<br>
        Larkspur Ridge, Virginia 23648<br>
        <b>T</b>: 757-555-0142 <b>|</b> <b>F</b>: 757-555-0199<br>
        <b>E</b>: marcy@mlplawgroup.example
      </address>
    </header>

    <section class="letter">
      <p class="salutation">Dear Mr. John,</p>
      <p class="body">Lorem Ipsum is simply dummy text of the printing and typesetting industry. Lorem Ipsum has been the industry's standard dummy text ever since the 1500s, when an unknown printer took a galley of type and scrambled it to make a type specimen book. It has survived not only five centuries, but also the leap into electronic typesetting, remaining essentially unchanged.</p>
      <p class="body">The standard chunk of Lorem Ipsum used since the 1500s is reproduced below for those interested. Sections 1.10.32 and 1.10.33 from "de Finibus Bonorum et Malorum" by Cicero are also reproduced in their exact original form, accompanied by English versions from the 1914 translation by H. Rackham</p>
      <p class="body">Lorem Ipsum is simply dummy text of the printing and typesetting industry. Lorem Ipsum has been the industry's standard dummy text ever since the 1500s, when an unknown printer took a galley of type and scrambled it to make a type specimen book. It has survived not only five centuries, but also the leap into electronic typesetting, remaining essentially unchanged. It was popularised in the</p>
      <p class="closing">Sincerely Your,</p>
      <p class="signature">your name</p>
      <p>Name Last Name<br>Company Name</p>
    </section>

    <footer class="footer">
      <div class="footer-specialty">Legacy &amp; Succession Counsel</div>
      <div class="footer-rule"></div>
      <div class="footer-slogan">Guarding Your Family Enterprise is my Calling</div>
    </footer>
  </main>
</body>
</html>
```